Brell Stone Company Business Cards

Front and Back Business Card - logo and text setup - cool design. I need workable photoshop or illustrator files so I can setup each employee card with design that is created
Updates

Hi everyone, thank you for the great entries. Please no more white and blue cards - there are so many already - black and silver only now please. thanks!

Target Market(s)

Construction Industry - Facility Managers

Industry/Entity Type

Construction

Contact Information for Business Card

I really like contemporary simplistic looks - clean neat....not opposed to seeing some black backrounds

Requirements
Must have
• Logo/website address with design on front only - www.brellstone-example.com (logo attached)
• Back:
• Name/Title/Company Address/Phone/email address
Nice to have
• Cool design
Should not have
• Nothing gimmicky like Fire or Water - since we are a Fire Protection company - it has all been done

```html
<!DOCTYPE html>
<html lang="en">
<head>
<meta charset="utf-8">
<title>Brell Stone Company Business Cards</title>
<link href="https://fonts.googleapis.com/css2?family=Open+Sans:ital,wght@0,400;0,700;0,800;1,400&display=swap" rel="stylesheet">
<style>
  :root {
    --page: #1e1e20;
    --card: #141415;
    --card-edge: #2a2a2c;
    --brand-blue: #0a2699;
    --brand-red: #ff2a2a;
    --text-light: #e6e6e6;
    --text-white: #ffffff;
  }
  * { margin: 0; padding: 0; box-sizing: border-box; }
  html, body { width: 1200px; height: 960px; overflow: hidden; }
  body {
    background: var(--page);
    font-family: "Open Sans", sans-serif;
    position: relative;
  }
  .card {
    position: absolute;
    left: 320px;
    width: 560px;
    height: 320px;
    border-radius: 4px;
    overflow: hidden;
    border: 1px solid var(--card-edge);
    background: radial-gradient(ellipse at 50% 40%, #232325 0%, var(--card) 75%);
  }
  .card-front { top: 90px; }
  .card-back { top: 530px; }

  .brand-name {
    font-family: "Open Sans", sans-serif;
    font-weight: 800;
    color: var(--brand-blue);
    letter-spacing: -0.5px;
    line-height: 1;
  }
  .card-front .brand-name {
    position: absolute;
    top: 110px;
    left: 0;
    width: 100%;
    text-align: center;
    font-size: 62px;
  }
  .card-front .website {
    position: absolute;
    top: 200px;
    width: 100%;
    text-align: center;
    color: var(--text-light);
    font-size: 15px;
    letter-spacing: 3px;
  }

  .card-back .brand-name {
    position: absolute;
    top: 22px;
    left: 26px;
    font-size: 40px;
  }
  .contact-list {
    position: absolute;
    top: 92px;
    left: 30px;
    list-style: none;
    color: var(--text-light);
    font-size: 13.5px;
  }
  .contact-list li {
    display: flex;
    align-items: center;
    gap: 8px;
    height: 22px;
  }
  .contact-list svg { width: 13px; height: 13px; flex: none; }
  .address {
    position: absolute;
    top: 164px;
    left: 30px;
    color: var(--text-light);
    font-size: 13.5px;
    line-height: 20px;
    font-style: normal;
  }
  .swoosh { position: absolute; left: 0; top: 0; width: 560px; height: 320px; }
  .person {
    position: absolute;
    right: 30px;
    bottom: 22px;
    text-align: right;
    color: var(--text-white);
  }
  .person-name { font-weight: 700; font-size: 19px; line-height: 24px; }
  .person-title { font-size: 16px; font-style: italic; line-height: 20px; }
</style>
</head>
<body>

<section class="card card-front" aria-label="Business card front">
  <div class="brand-name">Brell Stone</div>
  <div class="website">www.brellstone-example.com</div>
</section>

<section class="card card-back" aria-label="Business card back">
  <svg class="swoosh" viewBox="0 0 560 320" aria-hidden="true">
    <path d="M0,205 C90,245 210,282 330,290 C420,295 500,282 560,270 L560,320 L0,320 Z" fill="var(--brand-red)"/>
    <path d="M0,222 C90,262 210,296 330,302 C420,306 500,296 560,285 L560,320 L0,320 Z" fill="var(--card)"/>
    <path d="M0,185 C80,225 180,258 300,268 C400,276 490,262 560,250 L560,262 C490,274 400,286 300,280 C180,272 80,240 0,198 Z" fill="var(--brand-blue)"/>
    <path d="M230,320 C300,300 400,282 560,272 L560,320 Z" fill="var(--brand-blue)"/>
    <path d="M140,320 C230,300 330,286 420,282 C470,280 520,278 560,276 L560,320 Z" fill="var(--brand-blue)"/>
  </svg>

  <div class="brand-name">Brell Stone</div>

  <ul class="contact-list">
    <li>
      <svg viewBox="0 0 16 16" aria-hidden="true"><path d="M3.5 1.5l2.5 0 1 3.5-1.8 1.2c.9 1.9 2.3 3.3 4.2 4.2L10.6 8.6l3.5 1v2.5c0 .8-.7 1.5-1.5 1.5C7 13.6 2 8.6 2 3c0-.8.7-1.5 1.5-1.5z" fill="var(--brand-red)"/></svg>
      <span>(555) 014-2290</span>
    </li>
    <li>
      <svg viewBox="0 0 16 16" aria-hidden="true"><rect x="1" y="3" width="14" height="10" fill="var(--brand-red)"/><path d="M1 3l7 6 7-6" fill="none" stroke="var(--card)" stroke-width="1.4"/></svg>
      <span>info@brellstone-example.com</span>
    </li>
    <li>
      <svg viewBox="0 0 16 16" aria-hidden="true"><g fill="none" stroke="var(--brand-red)" stroke-width="1.4"><circle cx="8" cy="8" r="6.3"/><ellipse cx="8" cy="8" rx="2.8" ry="6.3"/><path d="M1.7 8h12.6M2.8 4.8h10.4M2.8 11.2h10.4"/></g></svg>
      <span>www.brellstone-example.com</span>
    </li>
  </ul>

  <address class="address">48 Quarry Lane<br>Millbrook, NY 10000</address>

  <div class="person">
    <div class="person-name">Dana Whitlock</div>
    <div class="person-title">President</div>
  </div>
</section>

</body>
</html>
```